project - Misto Den

Dear designers, I'm Looking for an appealing new business card design to represent us for our new e-cigarette store: The Misto Den. Knowledgeable and friendly staff we aim for superior customer service with a positive atmosphere. Classic feel with modern touch is what we are aiming for . Lime green font and grey back round is the original color scheme but we are flexible and open to suggestions. I added some doodles to show you where my mind is at. address: 4827 203 St SW Edmonton, AB (inside the grand swap bazaar)web: themistoden.com email: info@themistoden.com phone : 555.214.6093 Thanks and am looking forward to seeing your creative , fresh and innovative designs.
Good luck everybody!
Gordon
Updates
lime green and charcoal grey please. thanks
Industry/Entity Type
Business
Logo Text
The Misto Den
Look and feel
Each slider illustrates characteristics of the customer's brand and the style your logo design should communicate.

```html
<!DOCTYPE html>
<html lang="en">
<head>
<meta charset="UTF-8">
<title>The Misto Den — Business Card</title>
<link rel="stylesheet" href="https://fonts.googleapis.com/css2?family=Raleway:wght@400;500;600;700&display=swap">
<style>
  :root {
    --page: #f1f2f3;
    --charcoal: #2d3e4c;
    --charcoal-light: #3f5566;
    --lime: #c3f01a;
    --smoke: #a9b3b9;
    --paper: #e6ebee;
    --rule: #6e7f8b;
  }
  * { box-sizing: border-box; margin: 0; padding: 0; }
  html, body {
    width: 1200px; height: 1000px; overflow: hidden;
    background: var(--page);
    font-family: "Raleway", sans-serif;
  }
  .canvas { position: relative; width: 1200px; height: 1000px; }
  .card {
    position: absolute; left: 250px; width: 700px; height: 400px;
    background: var(--charcoal);
    overflow: hidden;
    box-shadow: 0 10px 30px rgba(0,0,0,.18);
  }
  .card--contact { top: 60px; }
  .card--brand {
    top: 540px;
    background: linear-gradient(100deg, var(--charcoal) 55%, var(--charcoal-light) 100%);
  }
  .tab { position: absolute; width: 26px; height: 150px; background: var(--lime); }
  .tab--left { left: 0; top: 125px; border-radius: 0 12px 12px 0; }
  .tab--right { right: 0; top: 60px; border-radius: 12px 0 0 12px; }
  .mark {
    position: absolute; left: 120px; top: 188px;
    display: flex; align-items: center; gap: 10px;
  }
  .mark__square { width: 12px; height: 12px; background: var(--smoke); }
  .mark__name { color: var(--smoke); font-weight: 500; font-size: 18px; }
  .contact {
    position: absolute; left: 370px; top: 140px;
    border-left: 1px solid var(--rule); padding-left: 16px;
    color: var(--lime); font-size: 15px; line-height: 1.45; font-style: normal;
  }
  .contact__name { font-weight: 700; font-size: 16px; }
  .contact__row { display: flex; align-items: center; gap: 8px; margin-top: 4px; }
  .contact__row svg { width: 16px; height: 16px; flex: none; }
  .brand-rule {
    position: absolute; left: 230px; top: 40px; width: 1px; height: 150px;
    background: var(--rule); transform: rotate(28deg); transform-origin: top;
  }
  .brand { position: absolute; right: 60px; top: 200px; text-align: right; }
  .brand__name {
    color: var(--paper); font-weight: 600; font-size: 52px; line-height: 1;
  }
  .brand__tagline {
    color: var(--lime); font-weight: 500; font-size: 32px; margin-top: 10px;
    letter-spacing: 1px;
  }
</style>
</head>
<body>
<main class="canvas">
  <section class="card card--contact">
    <span class="tab tab--left"></span>
    <span class="tab tab--right"></span>
    <div class="mark">
      <span class="mark__square"></span>
      <span class="mark__name">The Misto Den</span>
    </div>
    <address class="contact">
      <div class="contact__name">The Misto Den</div>
      <div>4827 203 St SW Edmonton</div>
      <div>AB (inside the grand swap bazaar)</div>
      <div class="contact__row">
        <svg viewBox="0 0 16 16"><circle cx="8" cy="8" r="6.5" fill="none" stroke="#c3f01a" stroke-width="1.2"/><path d="M1.5 8h13M8 1.5c-3 3.5-3 9.5 0 13M8 1.5c3 3.5 3 9.5 0 13" fill="none" stroke="#c3f01a" stroke-width="1"/></svg>
        <span>: themistoden.com</span>
      </div>
      <div class="contact__row">
        <svg viewBox="0 0 16 16"><rect x="1" y="3.5" width="14" height="9" fill="#c3f01a"/><path d="M1 3.5l7 5 7-5" fill="none" stroke="#2d3e4c" stroke-width="1.2"/></svg>
        <span>: info@themistoden.com</span>
      </div>
      <div class="contact__row">
        <svg viewBox="0 0 16 16"><path d="M4 1.5l2.5 3-1.5 1.8c.8 1.8 2 3 3.8 3.8l1.8-1.5 3 2.5-1.6 2.6C7 13.5 2.5 9 1.5 3.1z" fill="#c3f01a"/></svg>
        <span>: 555.214.6093</span>
      </div>
    </address>
  </section>

  <section class="card card--brand">
    <span class="brand-rule"></span>
    <div class="brand">
      <div class="brand__name">The Misto Den</div>
      <div class="brand__tagline">e-cigarette store</div>
    </div>
  </section>
</main>
</body>
</html>
```